Business Card Design for Occupational Medicine Start Up Company

We need to design a professional business card. We are a healthcare company providing occupational medicine services to blue collar industries. We are professional, efficient and high quality service providers.

Target Market(s)

Blue Collar Industry: Shipbuilding, Ports, Trucking Companies; The Executives and Safety Officers for these companies

Industry/Entity Type

Healthcare

Contact Information for Business Card

Logo, Name, Title, Email, Phone

Other font styles liked:
• Please match our Brand Guide

Requirements
Must have
• Our Company Colors and Logo

```html
<!DOCTYPE html>
<html lang="en">
<head>
<meta charset="utf-8">
<title>Crewline Clinics – Business Card</title>
<link href="https://fonts.googleapis.com/css2?family=Montserrat:wght@400;500;600;700&display=swap" rel="stylesheet">
<style>
  :root {
    --bg: #2b2b2b;
    --paper: #f4f4f2;
    --navy: #2e2f7a;
    --sky: #2ea3dc;
    --amber: #eaa93a;
    --ink: #2e2f7a;
  }
  * { margin: 0; padding: 0; box-sizing: border-box; }
  html, body {
    width: 1200px; height: 1200px; overflow: hidden;
    background: var(--bg);
    font-family: "Montserrat", Arial, sans-serif;
    color: var(--ink);
  }
  .stage { position: relative; width: 1200px; height: 1200px; }
  .card {
    position: absolute; width: 593px; height: 347px;
    background: var(--paper); border-radius: 20px; overflow: hidden;
  }
  .card--front { left: 298px; top: 200px; }
  .card--back  { left: 292px; top: 637px; }

  /* front */
  .front-mark {
    position: absolute; left: 262px; top: 80px;
    width: 70px; height: 70px; border-radius: 50%; background: var(--sky);
  }
  .front-name {
    position: absolute; left: 0; right: 0; top: 178px; text-align: center;
    font-weight: 700; color: var(--navy);
  }
  .front-name .line1 { display: block; font-size: 36px; line-height: 40px; letter-spacing: 0.5px; }
  .front-name .line2 { display: block; font-size: 18px; line-height: 24px; letter-spacing: 7px; padding-left: 7px; }
  .front-web {
    position: absolute; left: 0; right: 0; top: 299px; text-align: center;
    font-size: 16px; letter-spacing: 1.2px; color: var(--navy);
  }
  .front-web .accent { color: var(--sky); }

  /* back */
  .header-band {
    position: absolute; left: 0; top: 0; width: 593px; height: 96px;
    background: var(--navy);
  }
  .header-rule {
    position: absolute; left: 0; top: 102px; width: 593px; height: 5px;
    background: var(--amber);
  }
  .holder {
    position: absolute; right: 43px; top: 24px; text-align: right;
  }
  .holder-name { font-size: 25px; font-weight: 600; color: var(--sky); letter-spacing: 0.5px; line-height: 28px; }
  .holder-title { font-size: 15px; font-weight: 400; color: #ffffff; line-height: 20px; }
  .back-mark {
    position: absolute; left: 40px; top: 128px;
    width: 60px; height: 60px; border-radius: 50%; background: var(--sky);
  }
  .back-name {
    position: absolute; left: 131px; top: 132px; font-weight: 700; color: var(--navy);
  }
  .back-name .line1 { display: block; font-size: 29px; line-height: 32px; letter-spacing: 0.4px; }
  .back-name .line2 { display: block; font-size: 15px; line-height: 22px; letter-spacing: 6px; padding-left: 72px; }
  .contacts { position: absolute; left: 45px; top: 247px; list-style: none; }
  .contacts li, .address li {
    display: flex; align-items: center; gap: 12px;
    font-size: 16px; line-height: 21px; color: var(--navy);
  }
  .contacts svg, .address svg { width: 15px; height: 15px; flex: none; }
  .address { position: absolute; left: 332px; top: 268px; list-style: none; }
  .address li.indent { padding-left: 27px; }
</style>
</head>
<body>
<main class="stage">

  <section class="card card--front" aria-label="Card front">
    <div class="front-mark"></div>
    <h1 class="front-name"><span class="line1">CREWLINE</span><span class="line2">CLINICS</span></h1>
    <p class="front-web">www.<span class="accent">crewlineclinics</span>.com</p>
  </section>

  <section class="card card--back" aria-label="Card back">
    <div class="header-band"></div>
    <div class="header-rule"></div>
    <div class="holder">
      <p class="holder-name">DANIEL HARPER</p>
      <p class="holder-title">Senior Doctor</p>
    </div>

    <div class="back-mark"></div>
    <h2 class="back-name"><span class="line1">CREWLINE</span><span class="line2">CLINICS</span></h2>

    <ul class="contacts">
      <li>
        <svg viewBox="0 0 16 16" aria-hidden="true"><path d="M2 6 C2 3 14 3 14 6 L12 7.5 L10 6 V5 H6 V6 L4 7.5 Z M4 8.5 H12 L13 13 H3 Z" fill="var(--sky)"/></svg>
        555-014-2280
      </li>
      <li>
        <svg viewBox="0 0 16 16" aria-hidden="true"><rect x="1.5" y="3.5" width="13" height="9" fill="var(--navy)"/><path d="M1.5 3.5 L8 9 L14.5 3.5" fill="none" stroke="#fff" stroke-width="1.2"/></svg>
        daniel@crewline.com
      </li>
      <li>
        <svg viewBox="0 0 16 16" aria-hidden="true"><circle cx="8" cy="8" r="6" fill="none" stroke="var(--amber)" stroke-width="1.4"/><path d="M2 8 H14 M8 2 C5 5 5 11 8 14 M8 2 C11 5 11 11 8 14" fill="none" stroke="var(--amber)" stroke-width="1.1"/></svg>
        www.crewline.com
      </li>
    </ul>

    <ul class="address">
      <li>
        <svg viewBox="0 0 16 16" aria-hidden="true"><path d="M8 15 C4 10 3 8 3 6 A5 5 0 0 1 13 6 C13 8 12 10 8 15 Z" fill="var(--amber)"/><circle cx="8" cy="6" r="2" fill="var(--paper)"/></svg>
        48 Harbor Road, Suite 210
      </li>
      <li class="indent">Bayport, State 20418</li>
    </ul>
  </section>

</main>
</body>
</html>
```